RUVO WARE LTD

Advertisement to get more schools:
use website https://www.ruvo-ware.co.uk for logos etc.
ICT Service Level Agreements for as little as £2000 per year
Unlimited Remote, phone and email support
Unlimited Call outs included
90% fix time within 30 minutes of ticket submission
Extra support during Scolvar inspections
GDPR service included

Education

```html
<!DOCTYPE html>
<html lang="en">
<head>
<meta charset="utf-8">
<title>RUVO WARE LTD – ICT SLA Agreements</title>
<link href="https://fonts.googleapis.com/css2?family=Montserrat:wght@500;700;800&family=Poppins:wght@400;600;700&display=swap" rel="stylesheet">
<style>
  :root {
    --orange: #f07f45;
    --blue: #0872be;
    --brand-blue: #1f6fb5;
    --slate: #889cab;
    --slate-text: #8596a4;
    --white: #ffffff;
    --photo-deep: #1d3f73;
    --photo-glow: #7fc4f2;
  }
  * { box-sizing: border-box; margin: 0; padding: 0; }
  html, body { width: 880px; height: 1200px; overflow: hidden; background: var(--white); }
  body { font-family: "Montserrat", Arial, sans-serif; }
  .flyer { position: relative; width: 880px; height: 1200px; background: var(--white); overflow: hidden; }

  /* header */
  .brand { position: absolute; left: 145px; top: 100px; }
  .brand-name { display: flex; align-items: center; gap: 10px; font-weight: 800; font-size: 38px; line-height: 1; color: var(--brand-blue); letter-spacing: 0.5px; }
  .brand-square { width: 30px; height: 30px; background: var(--orange); }
  .brand-tagline { margin-top: 12px; font-weight: 500; font-size: 11.5px; letter-spacing: 1.1px; color: var(--brand-blue); }
  .social { position: absolute; left: 589px; top: 115px; display: flex; gap: 17px; }
  .social span { width: 34px; height: 34px; border-radius: 50%; background: var(--slate-text); }

  /* hero */
  .hero { position: absolute; left: 0; top: 194px; width: 880px; height: 296px; background: var(--slate); }
  .hero-photo { position: absolute; right: 0; top: 0; width: 376px; height: 296px;
    background: radial-gradient(circle at 70% 42%, var(--photo-glow) 0%, #3d78b8 22%, var(--photo-deep) 55%, rgba(136,156,171,0) 100%); }
  .hero-title { position: absolute; left: 149px; top: 86px; font-weight: 800; font-size: 51px; line-height: 44px; color: var(--white); letter-spacing: 0.3px; }
  .hero-price { position: absolute; left: 149px; top: 183px; display: flex; align-items: center; gap: 5px;
    font-family: "Poppins", Arial, sans-serif; font-size: 18px; color: var(--white); }
  .price-badge { background: var(--orange); padding: 1px 8px; }

  /* support tiles */
  .tile { position: absolute; top: 565px; width: 151px; height: 145px; }
  .tile-icon { height: 88px; background: var(--orange); display: flex; align-items: center; justify-content: center; }
  .tile-label { height: 57px; background: var(--blue); display: flex; align-items: center; justify-content: center; text-align: center;
    font-family: "Poppins", Arial, sans-serif; font-weight: 700; font-size: 11.5px; line-height: 16px; color: var(--white); letter-spacing: -0.3px; }
  .tile-remote { left: 152px; } .tile-phone { left: 357px; } .tile-email { left: 574px; }

  .callouts { position: absolute; left: 155px; top: 752px; width: 570px; text-align: center; font-weight: 800; font-size: 29.5px; color: var(--slate-text); letter-spacing: 0.2px; }
  .fix-banner { position: absolute; left: 155px; top: 813px; width: 570px; height: 81px; background: var(--blue);
    display: flex; align-items: center; justify-content: center; text-align: center;
    font-weight: 800; font-size: 26px; line-height: 29px; color: var(--white); }

  /* extras */
  .extra-icon { position: absolute; top: 936px; width: 67px; height: 63px; background: var(--orange); display: flex; align-items: center; justify-content: center; }
  .extra-text { position: absolute; top: 931px; font-weight: 800; font-size: 22px; line-height: 23.5px; color: var(--slate-text); }
  .icon-inspection { left: 156px; } .text-inspection { left: 239px; }
  .icon-gdpr { left: 509px; } .text-gdpr { left: 598px; }

  /* footer */
  .footer { position: absolute; left: 0; top: 1050px; width: 880px; height: 150px; background: var(--slate); color: var(--white); }
  .footer-contact { position: absolute; left: 149px; top: 46px; font-family: "Poppins", Arial, sans-serif; font-size: 14px; line-height: 19px; letter-spacing: 3.2px; }
  .footer-legal { position: absolute; left: 475px; top: 34px; font-family: "Poppins", Arial, sans-serif; font-size: 10.5px; line-height: 17px; letter-spacing: -0.3px; }
</style>
</head>
<body>
<main class="flyer">
  <header>
    <div class="brand">
      <div class="brand-name"><span class="brand-square"></span>RUVO WARE</div>
      <div class="brand-tagline">EDUCATION SUPPORT &amp; INSTALLATION</div>
    </div>
    <div class="social" aria-label="Social links"><span></span><span></span><span></span></div>
  </header>

  <section class="hero">
    <div class="hero-photo" role="img" aria-label="Photo of a child in profile with glowing blue science formulas"></div>
    <h1 class="hero-title">ICT SLA<br>AGREEMENTS</h1>
    <p class="hero-price">FOR AS LITTLE AS <span class="price-badge">£2000 PER YEAR</span></p>
  </section>

  <div class="tile tile-remote">
    <div class="tile-icon">
      <svg width="56" height="56" viewBox="0 0 56 56" fill="none" stroke="#111" stroke-width="2.5" stroke-linecap="round">
        <path d="M12 30v-4a16 16 0 0 1 32 0v4"/>
        <rect x="8" y="28" width="8" height="13" rx="2"/>
        <rect x="40" y="28" width="8" height="13" rx="2"/>
        <path d="M44 41c0 6-6 8-12 8h-4"/>
      </svg>
    </div>
    <div class="tile-label">UNLIMITED<br>REMOTE</div>
  </div>
  <div class="tile tile-phone">
    <div class="tile-icon">
      <svg width="60" height="60" viewBox="0 0 24 24" fill="none" stroke="#111" stroke-width="1.1" stroke-linejoin="round">
        <path d="M22 16.9v3a2 2 0 0 1-2.2 2 19.8 19.8 0 0 1-8.6-3.1 19.5 19.5 0 0 1-6-6A19.8 19.8 0 0 1 2.1 4.2 2 2 0 0 1 4.1 2h3a2 2 0 0 1 2 1.7c.1.9.4 1.9.7 2.8a2 2 0 0 1-.5 2.1L8 9.8a16 16 0 0 0 6 6l1.3-1.3a2 2 0 0 1 2.1-.4c.9.3 1.8.6 2.8.7a2 2 0 0 1 1.7 2z"/>
      </svg>
    </div>
    <div class="tile-label">UNLIMITED<br>PHONE</div>
  </div>
  <div class="tile tile-email">
    <div class="tile-icon">
      <svg width="58" height="58" viewBox="0 0 58 58" fill="none" stroke="#111" stroke-width="2.5" stroke-linejoin="round">
        <path d="M6 24l23-17 23 17v26H6z"/>
        <path d="M6 24l23 16 23-16"/>
        <path d="M6 50l18-13M52 50L34 37"/>
        <text x="29" y="28" text-anchor="middle" font-family="Poppins, Arial, sans-serif" font-size="15" font-weight="600" fill="#111" stroke="none">@</text>
      </svg>
    </div>
    <div class="tile-label">UNLIMITED<br>EMAIL SUPPORT</div>
  </div>

  <h2 class="callouts">UNLIMITED CALL OUTS INCLUDED</h2>
  <div class="fix-banner">90% FIX TIME WITHIN<br>30 MINUTES OF TICKET SUBMISSION</div>

  <div class="extra-icon icon-inspection">
    <svg width="40" height="40" viewBox="0 0 40 40" fill="none" stroke="#111" stroke-width="2.2" stroke-linecap="round" stroke-linejoin="round">
      <circle cx="20" cy="20" r="15"/>
      <path d="M13 20l5 5 9-10"/>
    </svg>
  </div>
  <p class="extra-text text-inspection">EXTRA SUPPORT<br>DURING SCOLVAR<br>INSPECTIONS</p>

  <div class="extra-icon icon-gdpr">
    <svg width="40" height="40" viewBox="0 0 40 40" fill="none" stroke="#111" stroke-width="2.2" stroke-linejoin="round">
      <rect x="9" y="18" width="22" height="17" rx="2"/>
      <path d="M13 18v-5a7 7 0 0 1 14 0v5"/>
      <circle cx="20" cy="26" r="2"/>
    </svg>
  </div>
  <p class="extra-text text-gdpr">GDPR<br>SERVICE<br>INCLUDED</p>

  <footer class="footer">
    <p class="footer-contact">info@ruvo-ware.co.uk<br>www.ruvo-ware.co.uk</p>
    <p class="footer-legal">RUVO WARE, is a registered UK Limited Company<br>Company Number: 04817253<br>VAT Number: GB318564207</p>
  </footer>
</main>
</body>
</html>
```